RW Framewell Inc Business cards

We need business cards using our existing logo but slightly modified. Right now the logo says RW Loadbearing Masonry. We want to keep the RW part of the design, but replace the Structural Concrete portion with "FRAMEWELL". Please see the attached file.
Ideally this would be a blank template so we can add Different Names, titles, and phone numbers later.
On the one side we want only the logo and on the other side the detail. I'm attaching an example for you to see.
Please reach out with any other questions. Our address and other details will be given out once we find a design we like.

Target Market(s)

Construction Industry

```html
<!DOCTYPE html>
<html lang="en">
<head>
<meta charset="utf-8">
<title>RW Framewell Inc — Business Cards</title>
<link rel="stylesheet" href="https://fonts.googleapis.com/css2?family=Arimo:ital,wght@0,400;0,700;1,400&display=swap">
<style>
  :root {
    --stage: #e9e7e4;
    --card: #2d2e31;
    --card-pattern: #26272a;
    --pattern-light: #333438;
    --brand-blue: #1f78c8;
    --edge-blue: #1a5fa8;
    --text-light: #f2f2f2;
  }
  * { box-sizing: border-box; margin: 0; padding: 0; }
  html, body {
    width: 1200px; height: 795px; overflow: hidden;
    background: var(--stage);
    font-family: "Arimo", Arial, sans-serif;
  }
  .canvas { position: relative; width: 1200px; height: 795px; }

  .card {
    position: absolute;
    width: 540px; height: 309px;
    background: var(--card);
    border-bottom: 4px solid var(--edge-blue);
    border-left: 2px solid var(--edge-blue);
    overflow: hidden;
  }

  /* Logo side */
  .card--front { left: 50px; top: 90px; }
  .front-texture {
    position: absolute; inset: 0;
    background: linear-gradient(135deg, var(--pattern-light), var(--card-pattern));
  }
  .front-mark {
    position: absolute; left: 232px; top: 196px;
    font-weight: 700; font-size: 44px; letter-spacing: 1px;
    color: var(--brand-blue); line-height: 1;
  }

  /* Detail side */
  .card--back { left: 610px; top: 400px; }
  .contact-name {
    position: absolute; left: 30px; top: 40px;
    font-weight: 700; font-size: 20px; letter-spacing: 0.5px;
    color: var(--brand-blue); text-transform: uppercase;
  }
  .contact-title {
    position: absolute; left: 30px; top: 64px;
    font-style: italic; font-size: 15px; color: var(--text-light);
  }
  .divider {
    position: absolute; left: 30px; right: 28px; top: 120px;
    height: 2px; background: var(--brand-blue);
  }
  .logo {
    position: absolute; right: 40px; top: 22px;
    color: var(--brand-blue); font-weight: 700; text-align: center;
  }
  .logo-initials { display: block; font-size: 62px; line-height: 1; letter-spacing: 2px; }
  .logo-word { display: block; font-size: 16px; letter-spacing: 9px; margin-top: 6px; margin-right: -9px; }

  .contact-list {
    position: absolute; left: 30px; top: 138px;
    list-style: none; color: var(--text-light); font-size: 14px;
  }
  .contact-list li { display: flex; align-items: center; gap: 8px; height: 21px; }
  .contact-list svg { width: 12px; height: 12px; fill: var(--brand-blue); flex: none; }

  .address {
    position: absolute; right: 34px; bottom: 30px;
    text-align: right; font-size: 15px; line-height: 1.35; color: var(--text-light);
  }
</style>
</head>
<body>
<main class="canvas">

  <section class="card card--front" aria-label="Business card, logo side">
    <div class="front-texture" role="img" aria-label="Embossed repeating monogram texture across the card"></div>
    <div class="front-mark">RW</div>
  </section>

  <section class="card card--back" aria-label="Business card, detail side">
    <p class="contact-name">Dana Whitcombe</p>
    <p class="contact-title">President</p>

    <div class="logo">
      <span class="logo-initials">RW</span>
      <span class="logo-word">FRAMEWELL</span>
    </div>

    <div class="divider"></div>

    <ul class="contact-list">
      <li>
        <svg viewBox="0 0 24 24" aria-hidden="true"><path d="M6.6 10.8a15 15 0 0 0 6.6 6.6l2.2-2.2c.3-.3.7-.4 1-.2 1.1.4 2.3.6 3.6.6.6 0 1 .4 1 1V20c0 .6-.4 1-1 1A17 17 0 0 1 3 4c0-.6.4-1 1-1h3.5c.6 0 1 .4 1 1 0 1.3.2 2.5.6 3.6.1.3 0 .7-.2 1z"/></svg>
        555-204-3170
      </li>
      <li>
        <svg viewBox="0 0 24 24" aria-hidden="true"><path d="M7 1h10a2 2 0 0 1 2 2v18a2 2 0 0 1-2 2H7a2 2 0 0 1-2-2V3a2 2 0 0 1 2-2zm0 3v14h10V4zm5 15.5a1 1 0 1 0 0 2 1 1 0 0 0 0-2z"/></svg>
        555-204-3185
      </li>
      <li>
        <svg viewBox="0 0 24 24" aria-hidden="true"><path d="M2 5h20v14H2zm2 2v.5l8 5 8-5V7zm0 2.8V17h16V9.8l-8 5z"/></svg>
        info@framewellbuild.com
      </li>
      <li>
        <svg viewBox="0 0 24 24" aria-hidden="true"><path d="M12 2a10 10 0 1 0 0 20 10 10 0 0 0 0-20zm6.9 9h-3a15 15 0 0 0-1.3-5.6A8 8 0 0 1 18.9 11zM12 4c.9 1.2 1.8 3.6 1.9 7h-3.8c.1-3.4 1-5.8 1.9-7zM9.4 5.4A15 15 0 0 0 8.1 11h-3a8 8 0 0 1 4.3-5.6zM5.1 13h3a15 15 0 0 0 1.3 5.6A8 8 0 0 1 5.1 13zm6.9 7c-.9-1.2-1.8-3.6-1.9-7h3.8c-.1 3.4-1 5.8-1.9 7zm2.6-1.4a15 15 0 0 0 1.3-5.6h3a8 8 0 0 1-4.3 5.6z"/></svg>
        www.framewellbuild.com
      </li>
    </ul>

    <address class="address" style="font-style: normal;">
      48 Millbrook Yard Lane<br>
      Hollis NY 12045
    </address>
  </section>

</main>
</body>
</html>
```